Modern Business Card

Modern professional business card with more than just logo and demographic info. Something memorable.

We are a trendy/modern chiropractic group with an emphasis on neurology, hence the minimalist-type brain logo. We want to convey that modern and technical aspect with professionalism and the elite nature of our practice environment.

```html
<!DOCTYPE html>
<html lang="en">
<head>
<meta charset="utf-8">
<title>Keystone Chiropractic — Business Card</title>
<link href="https://fonts.googleapis.com/css2?family=Cinzel:wght@600&family=Montserrat:wght@400;500&display=swap" rel="stylesheet">
<style>
  :root {
    --backdrop: #dde1e2;
    --paper: #f3f3f1;
    --brand-blue: #3f7cc4;
    --ink: #1c1c1c;
    --muted: #6b6b6b;
    --rule: #8a8a8a;
    --white: #ffffff;
    --emboss: rgba(0, 0, 0, 0.055);
    --frame-light: rgba(255, 255, 255, 0.35);
  }
  * { margin: 0; padding: 0; box-sizing: border-box; }
  html, body { width: 1200px; height: 852px; overflow: hidden; }
  body {
    background: var(--backdrop);
    display: flex;
    align-items: center;
    justify-content: center;
    gap: 60px;
    font-family: "Montserrat", sans-serif;
  }
  .card {
    width: 525px;
    height: 300px;
    position: relative;
    overflow: hidden;
    box-shadow: 0 6px 18px rgba(0,0,0,0.12);
  }
  .card-front { background: var(--paper); }
  .card-back {
    background: var(--brand-blue);
    display: flex;
    align-items: center;
    justify-content: center;
  }

  /* Large faint embossed block behind the front wordmark */
  .emboss-block {
    position: absolute;
    left: 350px;
    top: 112px;
    width: 150px;
    height: 150px;
    border-radius: 22px;
    background: var(--emboss);
  }

  /* Thin inset frame on the back for a precise, technical finish */
  .back-frame {
    position: absolute;
    inset: 18px;
    border: 1px solid var(--frame-light);
    pointer-events: none;
  }

  .wordmark {
    font-family: "Cinzel", serif;
    font-weight: 600;
    line-height: 0.95;
    display: flex;
    align-items: center;
    gap: 14px;
    position: relative;
  }
  .wordmark-mark { flex: none; }
  .wordmark-text span { display: block; }
  .card-front .wordmark {
    position: absolute;
    top: 46px;
    right: 34px;
    color: var(--ink);
    font-size: 30px;
  }
  .card-front .wordmark-mark { width: 26px; height: 26px; background: var(--brand-blue); }
  .card-front .wordmark-text span + span { font-size: 19px; letter-spacing: 0.04em; }
  .card-back .wordmark { color: var(--white); font-size: 50px; }
  .card-back .wordmark-mark { width: 40px; height: 40px; background: var(--white); }
  .card-back .wordmark-text span + span { font-size: 32px; letter-spacing: 0.04em; }

  .contact {
    position: absolute;
    left: 36px;
    top: 128px;
  }
  .contact-name {
    font-family: "Cinzel", serif;
    font-weight: 600;
    font-size: 19px;
    color: var(--brand-blue);
  }
  .contact-role { font-size: 13px; color: var(--muted); margin-top: 2px; }
  .contact-rule { width: 26px; height: 1px; background: var(--rule); margin: 14px 0 16px; }
  .contact-lines { font-size: 12.5px; color: var(--muted); line-height: 1.7; }
  .label { color: var(--brand-blue); font-weight: 500; }
  .web-domain { color: var(--brand-blue); }

  .card-front::after {
    content: "";
    position: absolute;
    left: 0; right: 0; bottom: 0;
    height: 4px;
    background: var(--brand-blue);
  }
</style>
</head>
<body>
  <section class="card card-front" aria-label="Business card front">
    <div class="emboss-block" aria-hidden="true"></div>
    <div class="wordmark">
      <div class="wordmark-mark" aria-hidden="true"></div>
      <div class="wordmark-text"><span>Keystone</span><span>Chiropractic</span></div>
    </div>
    <div class="contact">
      <p class="contact-name">Daniel Marlow</p>
      <p class="contact-role">Director</p>
      <div class="contact-rule"></div>
      <div class="contact-lines">
        <p>418 Cedar Ridge Lane, Salem, OR 97301</p>
        <p><span class="label">P:</span> (555) 014-2287 <span class="label">E:</span> hello@keystonechiro.com</p>
        <p>www.<span class="web-domain">keystonechiro</span>.com</p>
      </div>
    </div>
  </section>

  <section class="card card-back" aria-label="Business card back">
    <div class="back-frame" aria-hidden="true"></div>
    <div class="wordmark">
      <div class="wordmark-mark" aria-hidden="true"></div>
      <div class="wordmark-text"><span>Keystone</span><span>Chiropractic</span></div>
    </div>
  </section>
</body>
</html>
```